Pastor's Lantern: How To Help Church Leaders Remain Strong In Their Callings.

I have created a 250-page book tentatively entitled, Pastor's Lantern, subtitle: A Handbook To Help Church Leaders Remain Strong in Their Callings. The chapters are taken from my podcast of the same name on TuneVault and website: pastorslantern-example.com which will need updating soon. The purpose of the book is to provide practical solutions to pastors/leaders about everyday issues faced in ministry such as loneliness, financial challenges, a pastor's family problems, sexual temptation ...etc. You can get an idea of the topics from TuneVault.
Updates

As mentioned in the brief, I am looking for something that will communicate solutions. My podcast, Pastor's Lantern from which this material originates is all about practical help for local pastors in facing the challenges of daily ministry. The logo I sent was designed for concept purposes only. It does not need to be on the cover necessarily unless it feeds into the overall theme.

Target Market(s)

Pastors and Church Leaders in the Christian Faith

Industry/Entity Type

Religious

Font styles to use
Serif

Colors

Designer to choose colors to be used in the design.

Requirements
Must have
• Crisp copy and lines. People see covers for 3 seconds. If they are not drawn in by complicated themes, I have failed. Many of the designs so far do not address the topic of the book in a way that impacts. This is about a toolbox or book that provides solutions to their everyday challenges. If it doesn't somehow point to tools, it should instead point to getting solutions.
Nice to have
• I have included a copy of my current logo. If you can incorporate it, fine. If you have a better idea, I am open to that and would be interested in contributing more if the logo is superior. The logo is not essential to either front or back cover..
Should not have
• Simplistic religious themes from often used pics. I will peruse other book covers in my genre. If I find the same pic used, it disqualifies the design immediately no matter how much I like it. Target audience is ministers. Simplistic cross designs have gotten less votes so far in polling. I want to grab attention with a compelling picture that communicates solutions.

```html
<!DOCTYPE html>
<html lang="en">
<head>
<meta charset="utf-8">
<title>Pastor's Lantern — Book Cover</title>
<link rel="stylesheet" href="https://fonts.googleapis.com/css2?family=Cinzel:wght@400;500&display=swap">
<style>
  :root {
    --backdrop-light: #c4c4c4;
    --backdrop-mid: #acacac;
    --backdrop-dark: #959595;
    --steel-shine: #eef0f2;
    --steel-light: #c3c8cd;
    --steel-mid: #8b9096;
    --steel-dark: #3d4248;
    --ink: #ffffff;
    --ink-shadow: rgba(0, 0, 0, 0.28);
  }
  html, body {
    margin: 0;
    padding: 0;
    width: 737px;
    height: 1200px;
    overflow: hidden;
    background: var(--backdrop-mid);
  }
  .cover {
    position: relative;
    width: 737px;
    height: 1200px;
    overflow: hidden;
    font-family: "Cinzel", "Times New Roman", serif;
    color: var(--ink);
    text-align: center;
  }
  .cover-backdrop {
    position: absolute;
    inset: 0;
    background: linear-gradient(180deg, var(--backdrop-light) 0%, var(--backdrop-mid) 50%, var(--backdrop-dark) 100%);
  }
  .chain-photo {
    position: absolute;
    left: -120px;
    top: 640px;
    width: 1000px;
    height: 250px;
    transform: rotate(-17deg);
    transform-origin: center;
    border-radius: 125px;
    filter: blur(7px);
    background:
      linear-gradient(180deg,
        rgba(61,66,72,0) 0%,
        var(--steel-mid) 10%,
        var(--steel-shine) 22%,
        var(--steel-light) 32%,
        var(--steel-dark) 44%,
        var(--steel-mid) 54%,
        var(--steel-shine) 64%,
        var(--steel-light) 74%,
        var(--steel-dark) 88%,
        rgba(61,66,72,0) 100%);
    -webkit-mask-image: linear-gradient(90deg, rgba(0,0,0,0.55) 0%, #000 35%, #000 85%, rgba(0,0,0,0.7) 100%);
            mask-image: linear-gradient(90deg, rgba(0,0,0,0.55) 0%, #000 35%, #000 85%, rgba(0,0,0,0.7) 100%);
  }
  .title-block {
    margin: 0;
    font-weight: 400;
  }
  .series-word {
    position: absolute;
    top: 224px;
    left: 0;
    width: 100%;
    font-size: 52px;
    font-weight: 400;
    letter-spacing: 0.62em;
    padding-left: 0.62em;
    box-sizing: border-box;
    line-height: 1;
    text-shadow: 0 1px 2px var(--ink-shadow);
  }
  .main-title {
    position: absolute;
    top: 282px;
    left: 0;
    width: 100%;
    font-size: 120px;
    font-weight: 400;
    letter-spacing: 0.01em;
    line-height: 1;
    text-shadow: 0 1px 3px var(--ink-shadow);
  }
  .subtitle {
    position: absolute;
    top: 438px;
    left: 0;
    width: 100%;
    margin: 0;
    font-size: 20px;
    font-weight: 400;
    line-height: 33px;
    text-transform: uppercase;
    text-shadow: 0 1px 2px var(--ink-shadow);
  }
  .author {
    position: absolute;
    top: 1073px;
    left: 0;
    width: 100%;
    margin: 0;
    font-size: 34px;
    font-weight: 400;
    letter-spacing: 0.22em;
    padding-left: 0.22em;
    box-sizing: border-box;
    line-height: 1;
    text-transform: uppercase;
    text-shadow: 0 1px 2px var(--ink-shadow);
  }
</style>
</head>
<body>
  <main class="cover">
    <div class="cover-backdrop"></div>
    <div class="chain-photo" role="img" aria-label="Close-up photograph of heavy polished steel chain links crossing the cover diagonally against a soft grey background"></div>
    <h1 class="title-block">
      <span class="series-word">Pastor's</span>
      <span class="main-title">LANTERN</span>
    </h1>
    <p class="subtitle">A Handbook to Help Church Leaders<br>Remain Strong in Their Callings</p>
    <p class="author">Dana R. Whitfield</p>
  </main>
</body>
</html>
```